IT Services Company Needs Corporate PPT Template

This is urgent (need a fast turn around). We need a corporate PPT template deck (NOTE: Deck should be in 4:3 ratio) for our IT Services firm that is clean but slick and modern. We tend to lean more towards the flat design look. I'm attaching a zip file which includes our Corporate Branding Guide (which is in progress), color scheme, A PPT deck as inspiration (our logo is on the last slide), our font (LATO). Our newly launched website is located at: http://www.veranthix.com.

As an example of a deck we like see: http://slidemorrow.net/item/clean-multipurpose-business-presentation-template/5318206?WT.ac=category_thumb&WT.seg_1=category_thumb&WT.z_author=PixelHarbor
Although we don't want "this" deck - it gives an idea of style.

I'm also attaching a copy of our corporate deck as it is now to give you an idea of the type of content that would appear on various slides. We definitely want the following slides (at least) within the template:

Title Slide
Blank Slide
2 Column - with bullets
2 Column - no bullets
Single Column - no bullets
Single Column - with bullets
Various Charts and Tables (see example deck)
Meet the Team
Offering Slide
Customer Showcase
Timeline
Case Study
Contact US

Note: Being awarded this job will lead to a second job of creating our corporate deck.

Target Market(s)

CIO, CEO, Technology Officers, Sales People, Marketing, IT heads and staff, Customers, Prospective customers

Industry/Entity Type

Business

Requirements
Must have
• See description and attached files

```html
<!DOCTYPE html>
<html lang="en">
<head>
<meta charset="UTF-8">
<title>Project Title Here – Two Column Slide</title>
<link href="https://fonts.googleapis.com/css2?family=Lato:wght@400;700;900&family=Titillium+Web:wght@400&display=swap" rel="stylesheet">
<style>
  :root {
    --slide-bg: #efeeef;
    --brand-blue: #1f4e87;
    --brand-navy: #1c3d68;
    --title-grey: #4a4a4a;
    --body-text: #3a3a3a;
    --card-bg: #ffffff;
    --card-border: #d9d9d9;
    --placeholder-text: #c4c4c4;
    --footer-top: #f7f7f8;
    --footer-bottom: #d9dadc;
    --footer-text: #111111;
  }
  * { margin: 0; padding: 0; box-sizing: border-box; }
  html, body {
    width: 1200px;
    height: 900px;
    overflow: hidden;
    background: var(--slide-bg);
  }
  .slide {
    position: relative;
    width: 1200px;
    height: 900px;
    background: var(--slide-bg);
    font-family: "Lato", Arial, sans-serif;
  }
  .slide-header {
    position: absolute;
    left: 0;
    top: 27px;
    height: 69px;
    display: flex;
    align-items: center;
  }
  .slide-header__accent {
    width: 15px;
    height: 69px;
    background: var(--brand-blue);
  }
  .slide-header__title {
    margin-left: 12px;
    font-weight: 700;
    font-size: 48px;
    letter-spacing: -0.5px;
    color: var(--title-grey);
  }
  .slide-header__title .highlight { color: var(--brand-blue); }

  .column {
    position: absolute;
    top: 150px;
    width: 528px;
  }
  .column--left { left: 33px; }
  .column--right { left: 618px; top: 151px; }

  .media-placeholder {
    width: 528px;
    height: 210px;
    background: var(--card-bg);
    border: 1.5px solid var(--card-border);
    border-radius: 4px;
    display: flex;
    align-items: center;
    justify-content: center;
    font-family: "Titillium Web", Arial, sans-serif;
    font-size: 19px;
    letter-spacing: 0.5px;
    color: var(--placeholder-text);
  }
  .column__body {
    margin-top: 24px;
    font-size: 19.5px;
    line-height: 36px;
    color: var(--body-text);
  }
  .column__body p + p { margin-top: 36px; }

  .slide-footer {
    position: absolute;
    left: 0;
    bottom: 0;
    width: 1200px;
    height: 84px;
    border-top: 3px solid var(--brand-navy);
    background: linear-gradient(to bottom, var(--footer-top), var(--footer-bottom));
    display: flex;
    align-items: center;
    justify-content: space-between;
    padding: 0 31px 0 24px;
  }
  .brand-name {
    font-weight: 900;
    font-size: 40px;
    color: var(--brand-blue);
    letter-spacing: 0.5px;
  }
  .copyright {
    font-size: 18px;
    color: var(--footer-text);
  }
</style>
</head>
<body>
  <main class="slide">
    <header class="slide-header">
      <div class="slide-header__accent"></div>
      <h1 class="slide-header__title"><span class="highlight">PROJECT</span> TITLE HERE</h1>
    </header>

    <section class="column column--left">
      <div class="media-placeholder" role="img" aria-label="Project image placeholder">IMG HERE</div>
      <div class="column__body">
        <p>Lorem ipsum dolor sit ipsum Lorem ipsum dolor sit ipsum Lorem ipsum dolor sit ipsum Lorem ipsum dolor sit ipsum lorem ipsum dolor sit ipsum Lorem ipsum dolor sit ipsum Lorem ipsum dolor sit ipsum</p>
        <p>Lorem ipsum dolor sit ipsum Lorem ipsum dolor sit ipsum Lorem ipsum dolor sit ipsum Lorem ipsum dolor sit ipsum lorem ipsum dolor sit ipsum Lorem ipsum dolor sit ipsum Lorem ipsum dolor sit ipsum Lorem ipsum dolor sit ipsum</p>
      </div>
    </section>

    <section class="column column--right">
      <div class="media-placeholder" role="img" aria-label="Project image placeholder">IMG HERE</div>
      <div class="column__body">
        <p>Lorem ipsum dolor sit ipsum Lorem ipsum dolor sit ipsum Lorem ipsum dolor sit ipsum Lorem ipsum dolor sit ipsum lorem ipsum dolor sit ipsum Lorem ipsum dolor sit ipsum Lorem ipsum dolor sit ipsum</p>
        <p>Lorem ipsum dolor sit ipsum Lorem ipsum dolor sit ipsum Lorem ipsum dolor sit ipsum Lorem ipsum dolor sit ipsum lorem ipsum dolor sit ipsum Lorem ipsum dolor sit ipsum Lorem ipsum dolor sit ipsum Lorem ipsum dolor sit ipsum</p>
      </div>
    </section>

    <footer class="slide-footer">
      <span class="brand-name">Veranthix</span>
      <span class="copyright">Copyright text here</span>
    </footer>
  </main>
</body>
</html>
```